Wholesale in Gold Jewellery & Gold Bullion

We are an established gold jewellery and gold bullion wholesaler selling these products to international clients. We already have a name and logo of our company, hence please view attached current card design. We need a completely new design to compliment our business and industry and the final design should be new and elegant.

Contact Information for Business Card

New card details must be same as per current card. Like logo, name, tel no. & etc.

Colors

Designer to choose colors to be used in the design.

```html
<!DOCTYPE html>
<html lang="en">
<head>
<meta charset="utf-8">
<title>Suvarna &amp; Co – Business Card</title>
<link rel="stylesheet" href="https://fonts.googleapis.com/css2?family=Roboto+Slab:wght@500&family=Open+Sans:wght@400&display=swap">
<style>
  :root {
    --page-bg: #ecebe8;
    --card-gold: #da960f;
    --card-text: #ffffff;
    --disc: #f3f3f3;
    --brand-ink: #3a3a3a;
  }
  * { margin: 0; padding: 0; box-sizing: border-box; }
  html, body {
    width: 1200px; height: 900px; overflow: hidden;
    background: var(--page-bg);
  }
  .stage {
    width: 1200px; height: 900px;
    display: flex; align-items: center; justify-content: center;
  }
  .business-card {
    position: relative;
    width: 880px; height: 543px;
    background: var(--card-gold);
    color: var(--card-text);
    font-family: "Open Sans", Arial, sans-serif;
    box-shadow: 0 10px 30px rgba(0,0,0,0.18);
    overflow: hidden;
  }
  .holder {
    position: absolute; left: 54px; top: 70px;
  }
  .holder-name {
    font-family: "Roboto Slab", Georgia, serif;
    font-weight: 500;
    font-size: 29px;
    letter-spacing: 0.5px;
    line-height: 1.1;
  }
  .holder-role {
    font-size: 24px;
    line-height: 1.25;
  }
  .address {
    position: absolute; left: 52px; top: 263px;
    font-size: 24px; line-height: 1.32;
    font-style: normal;
  }
  .contact-list {
    position: absolute; left: 52px; top: 365px;
    list-style: none;
    font-size: 24px; line-height: 31.5px;
  }
  .contact-list li { display: flex; align-items: center; }
  .contact-icon {
    width: 22px; height: 22px; margin-right: 9px;
    fill: var(--card-text);
    flex: none;
  }
  .brand-disc {
    position: absolute;
    left: 385px; top: 34px;
    width: 472px; height: 472px;
    border-radius: 50%;
    background: radial-gradient(circle at 40% 35%, #ffffff 0%, var(--disc) 60%, #e4e4e4 100%);
    display: flex; align-items: center; justify-content: center;
  }
  .brand-name {
    font-family: "Roboto Slab", Georgia, serif;
    font-weight: 500;
    font-size: 46px;
    color: var(--brand-ink);
    text-align: center;
    line-height: 1.2;
    letter-spacing: 1px;
    margin-top: 40px;
  }
</style>
</head>
<body>
<main class="stage">
  <article class="business-card">
    <header class="holder">
      <h1 class="holder-name">ROHAN DESILVA</h1>
      <p class="holder-role">Director</p>
    </header>

    <address class="address">12 Orchid Lane,<br>Singapore 238801</address>

    <ul class="contact-list">
      <li>
        <svg class="contact-icon" viewBox="0 0 24 24" aria-hidden="true"><path d="M3 9c0-3 4-5 9-5s9 2 9 5v2h-5V9c-2-.8-6-.8-8 0v2H3z"/><path d="M6 13h12l2 7H4z"/></svg>
        +65 6100 2400
      </li>
      <li>
        <svg class="contact-icon" viewBox="0 0 24 24" aria-hidden="true"><path d="M7 2h10a1 1 0 0 1 1 1v18a1 1 0 0 1-1 1H7a1 1 0 0 1-1-1V3a1 1 0 0 1 1-1zm1 3v12h8V5zm4 13.5a1.2 1.2 0 1 0 0 2.4 1.2 1.2 0 0 0 0-2.4z"/></svg>
        +65 9123 4567
      </li>
      <li>
        <svg class="contact-icon" viewBox="0 0 24 24" aria-hidden="true"><path d="M7 3h10v5H7z"/><path d="M3 9h18v8h-3v-3H6v3H3z"/><path d="M7 15h10v6H7z"/></svg>
        +65 6200 5812
      </li>
      <li>
        <svg class="contact-icon" viewBox="0 0 24 24" aria-hidden="true"><path d="M3 6h18v1.5l-9 6-9-6z"/><path d="M3 9.5l9 6 9-6V18H3z"/></svg>
        rohan@suvarnaco.com
      </li>
    </ul>

    <div class="brand-disc">
      <p class="brand-name">SUVARNA &amp; CO<br>PTE LTD</p>
    </div>
  </article>
</main>
</body>
</html>
```